Need help in designing new business card utilizing our new logo.

BuildMark Solutions works with Construction Business Owners, Managers & IT Professionals to strengthen software usage and increase user productivity.

Our Construction Accounting and Mobile Field Management Software Clients engage with us in the following areas:

New Software Implementations
Software Re-Implementations
Redesigning Software Usage at the User Level
Project Coordination & Management
Continued Software Support

Old tag line:
Weighing Options - Implementing Solutions

www.buildmark-solutions.example

Ridge 4 is a product, but not needed for a new business card.

```html
<!DOCTYPE html>
<html lang="en">
<head>
<meta charset="utf-8">
<title>BuildMark Solutions – Business Card</title>
<link rel="stylesheet" href="https://fonts.googleapis.com/css2?family=PT+Sans:wght@400;700&display=swap">
<style>
  :root {
    --brand-blue: #1520a6;
    --ink-grey: #555555;
    --soft-grey: #b9b9bb;
    --card-white: #ffffff;
    --backdrop: #2e2e2e;
  }
  html, body {
    margin: 0;
    padding: 0;
    width: 1200px;
    height: 960px;
    overflow: hidden;
    background: var(--backdrop);
    font-family: "PT Sans", Arial, sans-serif;
  }
  .canvas {
    position: relative;
    width: 1200px;
    height: 960px;
  }
  .card {
    position: absolute;
    width: 600px;
    height: 342px;
    box-sizing: border-box;
    box-shadow: 0 4px 10px rgba(0,0,0,0.45);
  }
  /* Front */
  .card-front {
    left: 322px;
    top: 110px;
    background: var(--card-white);
  }
  .side-band {
    position: absolute;
    left: 0; top: 0;
    width: 56px;
    height: 100%;
    background: var(--brand-blue);
  }
  .brand-lockup {
    position: absolute;
    left: 30px;
    top: 32px;
    display: flex;
    align-items: center;
  }
  .brand-square {
    width: 40px;
    height: 40px;
    background: var(--brand-blue);
    border: 3px solid var(--card-white);
    margin-right: 18px;
  }
  .brand-divider {
    width: 2px;
    height: 58px;
    background: var(--brand-blue);
    margin-right: 10px;
  }
  .brand-name {
    color: var(--brand-blue);
    font-weight: 700;
    font-size: 34px;
    line-height: 1;
    letter-spacing: 0.5px;
  }
  .brand-name span {
    display: block;
    font-size: 12px;
    letter-spacing: 7px;
    margin-top: 3px;
  }
  .service-line {
    position: absolute;
    left: 95px;
    top: 104px;
    color: var(--ink-grey);
    font-size: 15px;
    line-height: 20px;
    text-transform: uppercase;
  }
  .contact-block {
    position: absolute;
    right: 30px;
    top: 193px;
    text-align: right;
    color: var(--ink-grey);
    font-size: 15px;
    line-height: 21px;
  }
  .person-name {
    color: var(--brand-blue);
    font-weight: 700;
    font-size: 21px;
    line-height: 24px;
    text-transform: uppercase;
  }
  .person-role {
    color: var(--soft-grey);
    font-weight: 700;
    font-size: 15px;
    line-height: 20px;
    margin-bottom: 4px;
  }
  .contact-gap { margin-top: 2px; }
  /* Back */
  .card-back {
    left: 320px;
    top: 493px;
    background: var(--brand-blue);
    color: var(--card-white);
  }
  .back-mark {
    position: absolute;
    left: 50px;
    top: 113px;
    width: 165px;
    display: flex;
    align-items: center;
    gap: 10px;
  }
  .back-mark-square {
    width: 18px;
    height: 18px;
    background: var(--card-white);
    flex: none;
  }
  .back-mark-name {
    font-weight: 700;
    font-size: 22px;
    letter-spacing: 0.5px;
  }
  .services {
    position: absolute;
    left: 236px;
    top: 77px;
    font-size: 15px;
    line-height: 19px;
  }
  .services-intro {
    font-weight: 700;
    text-transform: uppercase;
    margin: 0;
  }
  .services-list {
    list-style: none;
    margin: 0;
    padding: 0;
  }
  .services-list li::before {
    content: "• ";
  }
  .tagline {
    position: absolute;
    left: 0;
    width: 556px;
    top: 295px;
    text-align: center;
    font-size: 15px;
    text-transform: uppercase;
  }
</style>
</head>
<body>
<main class="canvas">
  <section class="card card-front" aria-label="Business card front">
    <div class="side-band"></div>
    <div class="brand-lockup">
      <div class="brand-square"></div>
      <div class="brand-divider"></div>
      <div class="brand-name">BUILDMARK<span>SOLUTIONS</span></div>
    </div>
    <div class="service-line">Construction Accounting<br>Software Consultants</div>
    <div class="contact-block">
      <div class="person-name">Dana R. Whitfield</div>
      <div class="person-role">OWNER</div>
      <div>14b harbor street-PMB118</div>
      <div>lakeview falls NY 10101</div>
      <div class="contact-gap">(P) 800-555-0142ext.100 (M) 555-555-0187</div>
      <div>dana@buildmark-solutions.example| buildmark-solutions.example</div>
    </div>
  </section>

  <section class="card card-back" aria-label="Business card back">
    <div class="back-mark">
      <div class="back-mark-square"></div>
      <div class="back-mark-name">BUILDMARK</div>
    </div>
    <div class="services">
      <p class="services-intro">Our construction accounting<br>and mobile field management<br>software clients engage with us<br>in the following areas:</p>
      <ul class="services-list">
        <li>New Software Implementations</li>
        <li>Software Re-Implementations</li>
        <li>Redesigning Software Usage at the User Level</li>
        <li>Project Coordination &amp; Management</li>
        <li>Continued Software Support</li>
      </ul>
    </div>
    <div class="tagline">Weighing Options - Implementing Solutions</div>
  </section>
</main>
</body>
</html>
```